2 x Digitize Logo | 2 x Business Cards | 2 x Fridge Magnets

We require 6 deliverables:
1. Residential logo redrawn (same just high quality for large print format).
2. Corporate logo redrawn (minor changes to wording and high quality for large print format).
3. New business card design for Furniture Removals (residential)
4. New business card design for Corporate Relocations (business)
5. New Fridge magnet for Furniture removals (residential)
6. New fridge magnet for Corporate Relocations (business)
1. Residential Logo
a. We require the logo to be translated into a high quality digital image with no modifications.
(see attached resilogo.jpg)
2. Residential Logo
a. We require the logo to be edited (add the word corporate relocations) be translated into a high quality digital image.
(see attached corplogo.jpg)
3. Using the resilogo please make a new business card for our business.
a. Please see the web site https://www.larkbendcarters.com.au for colours and inspiration.
b. The residential business card needs the following information:
i. Business Name (using the residential logo).
ii. Free Call: 1800 LB Cart (the L, B and Cart much be the same colour as the logo).
iii. Website: www.LarkbendCarters.com.au
iv. Address: 4/17 Ormsdale Court, VIC 3264
v. Email: cart@LarkbendCarters.com.au
vi. backof Card:
Review our service
www.PennantOrbit.com.au
Services: Local, Country, Interstate | Furniture Removals | Piano, Billiard Tables & Antiques
4. Using the corplogo please make a new business card for our business.
b. The corporate business card needs the following information:
i. Business Name (using the corporate logo).
v. Email: corporate@LarkbendCarters.com.au
vi. Back of Card:
Review our service
www.PennantOrbit.com.au
Services: Corporate relocations | Office equipment moves | Packing Service | Packing Materials
5. Using the resilogo please make a new fridge magent for our business.
b. The residential fidge magnet needs the following information:
iv. Services: Local, Country, Interstate | Furniture Removals | Piano, Billiard Tables & Antiques
6. Using the corplogo please make a new fridge magent for our business.
b. The corporate fidge magnet needs the following information:
iv. Services: Local, Country, Interstate | Corporate relocations
Target Market(s)
Residential Furniture Removals and Corporate Office relocations
Industry/Entity Type
Business
Contact Information for Business Card
Please see full brief for six items required
Requirements
Must have
- Clean simple, easy to read
Nice to have
- fresh, stand out, eye catching
Should not have
- plain, standard, boring, general

```html
<!DOCTYPE html>
<html lang="en">
<head>
<meta charset="utf-8">
<title>Larkbend Carters – Business Card</title>
<link rel="stylesheet" href="https://fonts.googleapis.com/css2?family=Source+Sans+3:ital,wght@0,400;0,700;0,900;1,400&display=swap">
<style>
  :root {
    --backdrop: #e6e3df;
    --card-white: #ffffff;
    --card-grey: #f2f2f2;
    --brand-green: #22b04b;
    --brand-red: #ed1c24;
    --brand-yellow: #fdc110;
    --ink: #222222;
    --ink-soft: #333333;
    --on-green: #ffffff;
  }
  * { box-sizing: border-box; margin: 0; padding: 0; }
  html, body {
    width: 1200px; height: 900px; overflow: hidden;
    background: var(--backdrop);
    font-family: "Source Sans 3", "Myriad Pro", Arial, sans-serif;
  }
  .stage { position: relative; width: 1200px; height: 900px; }

  .card { position: absolute; overflow: hidden; box-shadow: 0 6px 18px rgba(0,0,0,.18); }

  /* Front */
  .card-front { left: 107px; top: 35px; width: 588px; height: 362px; background: var(--card-white); }
  .card-front .bands { position: absolute; inset: 0; }
  .wordmark {
    position: absolute; left: 0; right: 0; top: 52px; text-align: center;
    font-weight: 900; font-size: 40px; letter-spacing: .5px;
    color: var(--brand-green); text-transform: uppercase; line-height: 1;
  }
  .contact-list { position: absolute; left: 24px; top: 253px; list-style: none; color: var(--on-green); font-size: 18px; line-height: 24.5px; }
  .contact-list li { display: flex; align-items: center; gap: 8px; }
  .contact-list svg { width: 13px; height: 13px; flex: none; }
  .address { position: absolute; right: 38px; top: 277px; text-align: right; color: var(--on-green); font-size: 18px; line-height: 24.5px; font-style: normal; }

  /* Back */
  .card-back { left: 388px; top: 505px; width: 567px; height: 352px; background: var(--card-grey); text-align: center; color: var(--ink); }
  .review-label { position: absolute; left: 0; right: 0; top: 99px; font-style: italic; font-size: 15px; color: var(--ink-soft); }
  .review-url { position: absolute; left: 0; right: 0; top: 120px; font-size: 20px; }
  .wordmark-faint {
    position: absolute; left: 0; right: 0; top: 158px;
    font-weight: 900; font-size: 52px; line-height: 1; text-transform: uppercase;
    color: var(--brand-green); opacity: .12;
  }
  .services-heading {
    position: absolute; left: 0; right: 0; top: 189px;
    display: flex; justify-content: center; align-items: center; gap: 6px;
    color: var(--brand-red); font-size: 15px; text-transform: uppercase;
  }
  .services-heading::before, .services-heading::after { content: ""; width: 44px; height: 3px; background: var(--brand-green); }
  .services-list { position: absolute; left: 0; right: 0; top: 223px; list-style: none; font-size: 16px; line-height: 20.5px; text-transform: uppercase; }
</style>
</head>
<body>
<main class="stage">

  <section class="card card-front" aria-label="Business card front">
    <svg class="bands" viewBox="0 0 588 362" width="588" height="362" aria-hidden="true">
      <polygon points="0,152 420,152 402,178 0,178" fill="var(--brand-yellow)"/>
      <polygon points="0,187 397,187 381,213 0,213" fill="var(--brand-red)"/>
      <polygon points="431,152 588,152 588,362 0,362 0,218 384,218" fill="var(--brand-green)"/>
    </svg>

    <div class="wordmark">Larkbend Carters</div>

    <ul class="contact-list">
      <li>
        <svg viewBox="0 0 16 16"><path fill="currentColor" d="M3.6 1.2l2.2 2.6c.3.4.3.9 0 1.2L4.6 6.3c.8 1.9 3.2 4.3 5.1 5.1l1.3-1.2c.3-.3.8-.3 1.2 0l2.6 2.2c.4.3.4.9.1 1.3l-1.2 1.3c-.5.5-1.3.7-2 .4C6.7 13.9 2.1 9.3.6 4.3c-.3-.7-.1-1.5.4-2L2.3 1.1c.4-.3.9-.3 1.3.1z"/></svg>
        <span>1800 LB Cart</span>
      </li>
      <li>
        <svg viewBox="0 0 16 16"><rect x="1" y="3" width="14" height="10" fill="currentColor"/><path d="M1.5 3.5L8 9l6.5-5.5" fill="none" stroke="var(--brand-green)" stroke-width="1.4"/></svg>
        <span>cart@LarkbendCarters.com.au</span>
      </li>
      <li>
        <svg viewBox="0 0 16 16"><circle cx="8" cy="8" r="7" fill="currentColor"/><path d="M1 8h14M8 1c-3 3-3 11 0 14M8 1c3 3 3 11 0 14" fill="none" stroke="var(--brand-green)" stroke-width="1.1"/></svg>
        <span>www.LarkbendCarters.com.au</span>
      </li>
    </ul>

    <address class="address">4/17 Ormsdale Court,<br>VIC 3264</address>
  </section>

  <section class="card card-back" aria-label="Business card back">
    <p class="review-label">Review our service</p>
    <p class="review-url">www.PennantOrbit.com.au</p>
    <div class="wordmark-faint" aria-hidden="true">Larkbend Carters</div>
    <h2 class="services-heading" style="font-weight:400">Services</h2>
    <ul class="services-list">
      <li>Local, Country, Interstate</li>
      <li>Furniture Removals</li>
      <li>Piano, Billiard Tables &amp; Antiques</li>
    </ul>
  </section>

</main>
</body>
</html>
```